Onboarding Infographic/brochure

We are a small criminal defense firm looking to create some sort of infographic or brochure that we can onboard new clients with. We are currently sending it out via email but want something a bit cooler and fun to send to clients. The information is:

A Few Quick Rules

We are here to help each step of the way. While questions are never discouraged, this letter will answer some of the most common ones we get asked.

Communications

As a client, you should always be in the loop. While we will try to respond to questions as quickly as possible, sometimes we are unable to respond right away. Do not worry - we promise to get back to you soon. Some questions might take some time to research, and a correct answer is better than a quick one.

Appointments

One of the benefits of having an attorney is the ability to discuss your case outside of court, minus the stress and headaches. If you need an appointment, please contact the office.

Appointments must be scheduled in advance. We do not want you to make a special trip to the office only to learn that we are in court or otherwise unavailable.

Jail Visits

If your family member is currently in jail, we take that very seriously. We will visit your loved one and introduce ourselves. While the case is ongoing, we ask that a family member be designated a “contact” person so that messages can be relayed quickly. Never discuss the facts of the case over the phone with someone who is in jail. Jail calls are recorded and we have seen too many cases go south based on remarks made over recorded lines.

Police Reports and Discovery

We will do our best to provide you with copies of everything we receive on your case. Most information will be emailed, so please keep your email address up to date.

Changes in Contact Information

If you move or change numbers during the case, please let us know. It is difficult to help if we are unable to reach you, and helping you is why we are here.

Court Appearances

Cases do not get resolved as quickly as they do on television. Expect there to be several hearings in your case and it may be necessary for you to attend one or more of them. If a hearing is set, you will receive notice of the date and time of each hearing.

Billing and Collections

We understand that this investment was a huge decision for you. As we focus on providing the best representation, we will need for you to stay on schedule with any payment arrangements agreed to at the time of your initial consultation.

Again, thank you for your trust in us. We look forward to getting a fantastic outcome on your case.

Target Market(s)

Criminal defense clients and their families

Industry/Entity Type

Legal

Font styles to use
Serif

Requirements
Must have
• Must incorporate all of the rules we email out. Would like diagrams, images or pictures
Nice to have
• We attached a Welcome brochure. Not sure I want it to look super similar, hence the request for infographic.

```html
<!DOCTYPE html>
<html lang="en">
<head>
<meta charset="utf-8">
<title>A Few Quick Rules</title>
<link rel="stylesheet" href="https://fonts.googleapis.com/css2?family=Lexend:wght@300;400;600;700&display=swap">
<style>
  :root {
    --cream: #fbf3e9;
    --ink: #000000;
    --accent: #1a9be0;
    --text: #f2f2f2;
    --muted: #6f7a85;
  }
  * { margin: 0; padding: 0; box-sizing: border-box; }
  html, body { width: 927px; height: 1200px; overflow: hidden; background: var(--cream); }
  body { position: relative; font-family: "Lexend", sans-serif; }
  .sheet {
    position: absolute; left: 18px; top: 22px; width: 891px; height: 1155px;
    background: var(--ink); border-radius: 50px; overflow: hidden;
  }
  .title {
    position: absolute; left: 0; right: 0; top: 72px; text-align: center;
    color: #fff; font-weight: 700; font-size: 36px; letter-spacing: -1px; line-height: 1;
  }
  .title .title-a { color: var(--accent); }
  .rule-line { position: absolute; top: 95px; height: 2px; width: 54px; }
  .rule-line.left { left: 196px; background: linear-gradient(90deg, transparent, var(--accent)); }
  .rule-line.right { left: 640px; background: linear-gradient(90deg, var(--accent), transparent); }
  .rail { position: absolute; left: 0; top: 0; width: 891px; height: 1155px; }
  .rule {
    position: absolute; left: 180px; width: 690px;
  }
  .rule h2 {
    color: var(--accent); font-weight: 600; font-size: 16.5px; line-height: 20px;
    letter-spacing: -0.3px; margin-bottom: 13px;
  }
  .rule p {
    color: var(--text); font-weight: 300; font-size: 11.4px; line-height: 25.8px;
  }
</style>
</head>
<body>
<main class="sheet">
  <span class="rule-line left"></span>
  <h1 class="title"><span class="title-a">A</span> FEW QUICK RULES</h1>
  <span class="rule-line right"></span>

  <svg class="rail" viewBox="0 0 891 1155" aria-hidden="true">
    <defs>
      <g id="ring">
        <circle r="45" fill="none" stroke="var(--muted)" stroke-width="1.2" stroke-linecap="round" stroke-dasharray="0.1 3.6"/>
        <circle r="45" fill="none" stroke="var(--accent)" stroke-width="3.6" stroke-linecap="round" stroke-dasharray="150 300" transform="rotate(-58)"/>
      </g>
      <marker id="tip" viewBox="0 0 6 6" refX="3" refY="5" markerWidth="6" markerHeight="6" orient="auto-start-reverse">
        <path d="M0.5 1 L3 5 L5.5 1" fill="none" stroke="var(--accent)" stroke-width="1"/>
      </marker>
    </defs>

    <g stroke="var(--accent)" stroke-width="0.8" stroke-dasharray="1.5 1.5" marker-end="url(#tip)">
      <line x1="94" y1="241" x2="94" y2="274"/>
      <line x1="94" y1="379" x2="94" y2="411"/>
      <line x1="94" y1="516" x2="94" y2="574"/>
      <line x1="94" y1="679" x2="94" y2="708"/>
      <line x1="94" y1="813" x2="94" y2="847"/>
      <line x1="94" y1="952" x2="94" y2="987"/>
    </g>

    <use href="#ring" x="94" y="188"/>
    <use href="#ring" x="94" y="326"/>
    <use href="#ring" x="94" y="463"/>
    <use href="#ring" x="94" y="626"/>
    <use href="#ring" x="94" y="760"/>
    <use href="#ring" x="94" y="899"/>
    <use href="#ring" x="94" y="1039"/>

    <g fill="none" stroke="var(--accent)" stroke-width="1.3" stroke-linejoin="round" stroke-linecap="round">
      <!-- chat -->
      <rect x="76" y="170" width="36" height="36" rx="3" stroke-dasharray="5 4"/>
      <path d="M82 178 h18 v11 h-10 l-4 4 v-4 h-4 z" stroke="#fff"/>
      <path d="M91 183 h18 v11 h-4 v4 l-4 -4 h-10 z"/>
      <line x1="95" y1="187" x2="105" y2="187"/><line x1="95" y1="190" x2="103" y2="190"/>
      <!-- calendar -->
      <rect x="74" y="310" width="34" height="32" rx="2"/>
      <line x1="74" y1="317" x2="108" y2="317"/>
      <line x1="81" y1="307" x2="81" y2="312"/><line x1="101" y1="307" x2="101" y2="312"/>
      <path d="M79 322 h4 v4 h-4z M86 322 h4 v4 h-4z M93 322 h4 v4 h-4z M79 330 h4 v4 h-4z M86 330 h4 v4 h-4z"/>
      <circle cx="106" cy="339" r="8" fill="var(--ink)" stroke="#fff"/>
      <path d="M106 334 v5 h4" stroke="#fff"/>
      <!-- bars -->
      <rect x="74" y="444" width="40" height="38"/>
      <line x1="74" y1="448" x2="114" y2="448"/><line x1="74" y1="478" x2="114" y2="478"/>
      <line x1="81" y1="448" x2="81" y2="478"/><line x1="88" y1="448" x2="88" y2="478" stroke="#fff"/>
      <line x1="94" y1="448" x2="94" y2="478"/><line x1="100" y1="448" x2="100" y2="478" stroke="#fff"/>
      <line x1="107" y1="448" x2="107" y2="478"/>
      <!-- report -->
      <rect x="77" y="606" width="28" height="38" rx="3"/>
      <path d="M84 616 l7 -3 l7 3 v5 c0 5 -4 7 -7 8 c-3 -1 -7 -3 -7 -8 z" stroke="#fff"/>
      <line x1="82" y1="634" x2="96" y2="634"/><line x1="82" y1="638" x2="92" y2="638"/>
      <path d="M113 615 l-16 18 l-2 5 l5 -2 l16 -18 z"/>
      <!-- contact card -->
      <rect x="74" y="744" width="38" height="32" rx="2"/>
      <line x1="78" y1="740" x2="108" y2="740"/>
      <rect x="79" y="751" width="12" height="16" rx="1" stroke="#fff"/>
      <line x1="96" y1="752" x2="107" y2="752"/><line x1="96" y1="758" x2="107" y2="758"/><line x1="96" y1="764" x2="104" y2="764"/>
      <!-- courthouse -->
      <path d="M74 890 l20 -10 l20 10 z"/>
      <line x1="74" y1="893" x2="114" y2="893"/>
      <line x1="79" y1="896" x2="79" y2="912"/><line x1="86" y1="896" x2="86" y2="912"/>
      <line x1="102" y1="896" x2="102" y2="912"/><line x1="109" y1="896" x2="109" y2="912"/>
      <path d="M90 912 v-12 h8 v12" stroke="#fff"/>
      <rect x="73" y="912" width="42" height="4"/>
      <!-- billing -->
      <rect x="94" y="1020" width="14" height="34"/>
      <line x1="97" y1="1025" x2="105" y2="1025"/><line x1="97" y1="1030" x2="105" y2="1030"/><line x1="97" y1="1035" x2="105" y2="1035"/>
      <path d="M90 1054 h22"/>
      <circle cx="84" cy="1030" r="7" stroke="#fff"/>
      <path d="M86 1027 h-3 a1.5 1.5 0 0 0 0 3 h2 a1.5 1.5 0 0 1 0 3 h-3 M84 1025 v10" stroke="#fff" stroke-width="1"/>
      <path d="M72 1042 h8 l6 3 h6 v6 h-6 l-6 3 h-8 z"/>
    </g>
  </svg>

  <section class="rule" style="top:138px">
    <h2>COMMUNICATIONS</h2>
    <p>As a client, you should always be in the loop. While we will try to respond to questions as quickly as possible, sometimes we are unable to respond right away. Do not worry - we promise to get back to you soon. Some questions might take some time to research, and a correct answer is better than a quick one.</p>
  </section>
  <section class="rule" style="top:276px">
    <h2>APPOINTMENTS</h2>
    <p>One of the benefits of having an attorney is the ability to discuss your case outside of court, minus the stress and headaches. If you need an appointment, please contact the office. Appointments must be scheduled in advance. We do not want you to make a special trip to the office only to learn that we are in court or otherwise unavailable.</p>
  </section>
  <section class="rule" style="top:413px">
    <h2>JAIL VISITS</h2>
    <p>If your family member is currently in jail, we take that very seriously. We will visit your loved one and introduce ourselves. While the case is ongoing, we ask that a family member be designated a “contact” person so that messages can be relayed quickly. Never discuss the facts of the case over the phone with someone who is in jail. Jail calls are recorded and we have seen too many cases go south based on remarks made over recorded lines.</p>
  </section>
  <section class="rule" style="top:576px">
    <h2>POLICE REPORTS AND DISCOVERY</h2>
    <p>We will do our best to provide you with copies of everything we receive on your case. Most information will be emailed, so please keep your email address up to date.</p>
  </section>
  <section class="rule" style="top:710px">
    <h2>CHANGES IN CONTACT INFORMATION</h2>
    <p>If you move or change numbers during the case, please let us know. It is difficult to help if we are unable to reach you, and helping you is why we are here.</p>
  </section>
  <section class="rule" style="top:848px">
    <h2>COURT APPEARANCES</h2>
    <p>Cases do not get resolved as quickly as they do on television. Expect there to be several hearings in your case and it may be necessary for you to attend one or more of them. If a hearing is set, you will receive notice of the date and time of each hearing.</p>
  </section>
  <section class="rule" style="top:989px">
    <h2>BILLING AND COLLECTIONS</h2>
    <p>We understand that this investment was a huge decision for you. As we focus on providing the best representation, we will need for you to stay on schedule with any payment arrangements agreed to at the time of your initial consultation.<br>Again, thank you for your trust in us. We look forward to getting a fantastic outcome on your case.</p>
  </section>
</main>
</body>
</html>
```